Brintel Works - Fast, Efficient and Gas Mainteance for Domestic, Commercial and Industrial clients

We are in the process of purchasing a new business and would like to get a new logo and business card.
Business is a gas maintenance business that also does new gas installations.
Has been established since 1988.
Services include:
Install all types of gas appliances & equipment inc. hot water units
Maintain / repair / replace all types of gas appliances & equipment

Target Market(s)

Domestic, Commercial and Industrial clients

Industry/Entity Type

Business

Contact Information for Business Card

admin@brintelworks.com.au
07 3918 4726
Brintel Works PTY LTD

Logo Text

Gas Fitting & Plumbing Maintenance Specialists

Font styles to use
Sans Serif

Requirements
Must have
• Logo
• Business name, contact number, email address, web address
• Domestic | Commercial | Industrial Est Since 1988
Nice to have
• Possibly a black card with a flame logo to one side
Should not have
• Spelling errors

```html
<!DOCTYPE html>
<html lang="en">
<head>
<meta charset="utf-8">
<title>Brintel Works – Business Card</title>
<link href="https://fonts.googleapis.com/css2?family=Source+Sans+3:wght@400;600;700&display=swap" rel="stylesheet">
<style>
  :root {
    --stage: #000000;
    --card: #323336;
    --divider: #45464a;
    --text: #f2f2f2;
    --accent: #f4a21f;
    --flame-red: #e8262a;
  }
  html, body {
    margin: 0;
    padding: 0;
    width: 1200px;
    height: 900px;
    overflow: hidden;
    background: var(--stage);
    font-family: "Source Sans 3", Arial, sans-serif;
  }
  .canvas {
    position: relative;
    width: 1200px;
    height: 900px;
  }
  .card {
    position: absolute;
    top: 271px;
    width: 457px;
    height: 281px;
    background: var(--card);
    border-radius: 14px;
  }
  .card--front { left: 137px; }
  .card--back { left: 626px; }

  .front-brand {
    position: absolute;
    left: 40px;
    top: 100px;
    width: 132px;
    text-align: center;
    color: var(--accent);
    font-weight: 700;
    font-size: 26px;
    line-height: 1.1;
  }
  .divider {
    position: absolute;
    left: 195px;
    top: 74px;
    width: 1px;
    height: 122px;
    background: var(--divider);
  }
  .address {
    position: absolute;
    left: 230px;
    top: 79px;
    margin: 0;
    color: var(--text);
    font-size: 13.5px;
    line-height: 19px;
    font-style: normal;
  }
  .contacts {
    position: absolute;
    left: 230px;
    top: 140px;
    margin: 0;
    padding: 0;
    list-style: none;
    color: var(--text);
    font-size: 13.5px;
    line-height: 19px;
  }
  .contacts li {
    display: flex;
    align-items: center;
    gap: 8px;
  }
  .contacts svg {
    width: 10px;
    height: 10px;
    flex: none;
  }
  .services {
    position: absolute;
    left: 0;
    right: 0;
    top: 232px;
    margin: 0;
    text-align: center;
    padding-right: 6px;
    color: var(--accent);
    font-weight: 600;
    font-size: 13.5px;
  }

  .back-mark {
    position: absolute;
    left: 194px;
    top: 74px;
    width: 70px;
    height: 70px;
    border-radius: 50%;
    background: var(--flame-red);
  }
  .back-name {
    position: absolute;
    left: 0;
    right: 0;
    top: 174px;
    margin: 0;
    text-align: center;
    color: var(--accent);
    font-weight: 700;
    font-size: 30px;
    line-height: 1;
  }
  .back-name .legal {
    display: block;
    margin-top: 6px;
    font-size: 11px;
    letter-spacing: 2px;
  }
</style>
</head>
<body>
<main class="canvas">

  <section class="card card--front" aria-label="Business card front">
    <div class="front-brand">Brintel<br>Works</div>
    <div class="divider"></div>
    <address class="address">12345, Address Goes Here<br>Country Name, 123456</address>
    <ul class="contacts">
      <li>
        <svg viewBox="0 0 10 10" aria-hidden="true"><path fill="var(--accent)" d="M2 0.5 L3.6 2.6 L2.7 3.6 Q3.8 5.9 6.3 7.2 L7.3 6.3 L9.5 7.9 L8.4 9.5 Q3.5 9 0.6 1.7 Z"/></svg>
        07 3918 4726
      </li>
      <li>
        <svg viewBox="0 0 10 10" aria-hidden="true"><rect x="0.5" y="2" width="9" height="6.5" fill="var(--accent)"/><path d="M0.8 2.3 L5 5.6 L9.2 2.3" fill="none" stroke="var(--card)" stroke-width="1"/></svg>
        admin@brintelworks.com.au
      </li>
      <li>
        <svg viewBox="0 0 10 10" aria-hidden="true"><g fill="none" stroke="var(--accent)" stroke-width="1.4" stroke-linecap="round"><path d="M4.2 5.8 L5.8 4.2"/><path d="M3.5 4.6 L2 6.1 A1.4 1.4 0 0 0 3.9 8 L5.4 6.5"/><path d="M6.5 5.4 L8 3.9 A1.4 1.4 0 0 0 6.1 2 L4.6 3.5"/></g></svg>
        www.brintelworks.com.au
      </li>
    </ul>
    <p class="services">Domestic | Commercial | Industrial Est Since 1988</p>
  </section>

  <section class="card card--back" aria-label="Business card back">
    <div class="back-mark"></div>
    <h1 class="back-name">Brintel Works<span class="legal">PTY LTD</span></h1>
  </section>

</main>
</body>
</html>
```